Business Cards Design for the electrical wholesaler: clean bold dynamic :)

We need a business card design that would follow our latest brand guidelines. As an electrical wholesaler we want to bring a fresh look and feel into the industry. The design should be clean bold and dynamic. It should come alive with the renewed energy of our green colour. Our grey colour should keep things balanced and complement the notion of maturity and responsibility. We employ Lato as a corporate font however are not bound by this font and we’re open to interpretation here.

Target Market(s)

Electrical contractors

Industry/Entity Type

Business

Contact Information for Business Card

Logo
Name & Surname: Halyna Dorosh
Job Title: Director of Marketing
Email: halya.dorosh@quillmail.example
Cell phone: XXX.XXX.XXXX
Address: 20517 - 87 Ave. Edmonton, AB, Canada. T6K 4N8
Business Phone: 780.555.0184
Website: www.brovix.example

Font styles to use
Other font styles liked:
• Lato

Requirements
Must have
• Logo & website
Nice to have
• Brand elements - some of them you may find in the attached Brand Guidelines (e.g. three lines on the background signifying "W")

```html
<!DOCTYPE html>
<html lang="en">
<head>
<meta charset="utf-8">
<title>Brovix business card</title>
<link href="https://fonts.googleapis.com/css2?family=Roboto:wght@500&family=Work+Sans:wght@400;500;600&display=swap" rel="stylesheet">
<style>
  :root {
    --green: #8dc63f;
    --grey: #58595b;
    --ink: #3a3a3a;
    --paper: #ffffff;
    --stage: #1b1b1b;
    --back-dark: #1c1c1c;
    --back-light: #363636;
  }
  * { margin: 0; padding: 0; box-sizing: border-box; }
  html, body { width: 1200px; height: 897px; overflow: hidden; background: var(--stage); }
  .canvas { position: relative; width: 1200px; height: 897px; }

  .card { position: absolute; left: 303px; width: 595px; height: 338px; border-radius: 18px; overflow: hidden; }
  .card-front { top: 92px; background: var(--paper); }
  .card-back { top: 469px; background: linear-gradient(135deg, var(--back-dark) 35%, var(--back-light) 100%); }

  .accent-block { position: absolute; left: 0; top: 38px; width: 24px; height: 63px; background: var(--grey); }
  .name-band { position: absolute; left: 31px; top: 38px; width: 388px; height: 63px; background: var(--green); color: var(--paper); padding: 7px 0 0 13px; }
  .person-name { font-family: "Roboto", sans-serif; font-weight: 500; font-size: 24px; line-height: 1.1; }
  .person-title { font-family: "Work Sans", sans-serif; font-size: 14.5px; letter-spacing: 0.5px; margin-top: 1px; }

  .brand-front { position: absolute; left: 428px; top: 44px; font-family: "Work Sans", sans-serif; font-weight: 600; font-size: 40px; color: var(--green); line-height: 1; }

  .contact-list { position: absolute; left: 36px; top: 255px; list-style: none; font-family: "Work Sans", sans-serif; font-size: 14.5px; color: var(--ink); }
  .contact-list li { display: flex; align-items: center; height: 19px; }
  .contact-list svg { width: 10px; height: 10px; margin-right: 11px; flex: none; }
  .contact-list .highlight { color: var(--green); }

  .address { position: absolute; right: 40px; top: 255px; text-align: right; font-family: "Work Sans", sans-serif; font-size: 14.5px; color: var(--ink); line-height: 19px; letter-spacing: 0.3px; }

  .bottom-bands { position: absolute; left: 0; bottom: 0; width: 595px; height: 27px; }

  .brand-lockup { position: absolute; inset: 0; display: flex; align-items: center; justify-content: center; gap: 16px; }
  .brand-dot { width: 26px; height: 26px; border-radius: 50%; background: var(--green); }
  .brand-back { font-family: "Work Sans", sans-serif; font-weight: 500; font-size: 72px; color: var(--paper); line-height: 1; letter-spacing: 1px; }
</style>
</head>
<body>
<div class="canvas">
  <section class="card card-front">
    <div class="accent-block"></div>
    <div class="name-band">
      <div class="person-name">Halyna Dorosh</div>
      <div class="person-title">Founder</div>
    </div>
    <div class="brand-front">brovix</div>

    <ul class="contact-list">
      <li>
        <svg viewBox="0 0 10 10"><path d="M2 0.5 L3.6 0.5 L4 3 L3 3.8 Q4 6 6.2 7 L7 6 L9.5 6.4 L9.5 8 Q9.5 9.5 8 9.5 Q1 8.5 0.5 2 Q0.5 0.5 2 0.5Z" fill="var(--green)"/></svg>
        780.555.0184
      </li>
      <li>
        <svg viewBox="0 0 10 10"><rect x="0.8" y="2" width="8.4" height="6" fill="none" stroke="var(--green)" stroke-width="1"/><path d="M0.8 2 L5 5.4 L9.2 2" fill="none" stroke="var(--green)" stroke-width="1"/></svg>
        hello@brovix.example
      </li>
      <li>
        <svg viewBox="0 0 10 10"><circle cx="5" cy="5" r="4.2" fill="none" stroke="var(--green)" stroke-width="0.9"/><ellipse cx="5" cy="5" rx="1.8" ry="4.2" fill="none" stroke="var(--green)" stroke-width="0.8"/><path d="M0.8 5 H9.2 M1.5 3 H8.5 M1.5 7 H8.5" stroke="var(--green)" stroke-width="0.7"/></svg>
        <span>www.<span class="highlight">brovix</span>.example</span>
      </li>
    </ul>

    <div class="address">
      20517 87ave<br>
      T6K4N8 Edmonton, Alberta
    </div>

    <svg class="bottom-bands" viewBox="0 0 595 27" preserveAspectRatio="none">
      <rect x="0" y="14" width="310" height="13" fill="var(--grey)"/>
      <polygon points="333,0 595,0 595,27 305,27" fill="var(--green)"/>
    </svg>
  </section>

  <section class="card card-back">
    <div class="brand-lockup">
      <span class="brand-dot"></span>
      <span class="brand-back">brovix</span>
    </div>
  </section>
</div>
</body>
</html>
```